I need a complete stationary pack for a real estate office that sells and manages residential proper

We need a stationary design pack for my real estate office called ‘brightkeyhomes’ that is in Queensland Australia. My offices are both in suburban and coastal locations in the south west corner of Queensland at the Coral Bay Shore and Brisbane.
We predominately manage real estate on behalf of owners and sell property in the residential sector.
I have attached a copy of our existing design of my business card and do like the current concept/layout. In saying this you may be able to use this existing theme across to the other items required or see opportunity on how to improve what I have already.
I would like to see concepts for the following products:
- Letterhead
- Fax header
- Business cards
- Email signature
- With complements slips and
- Envelopes
I have attached our current logo that was designed by Artfolder and the font is Prelo.

I am looking for a contemporary design that is professional and reflects trust and professionalism. I am currently using the logo with a black background on some material as per the following link

http://www.plotlisting.com.au/property/for-sale/house/qld/merridale/?adid=4827305118&sp=7

I have posted another job 517362 for signage and the company car signage done too if you are interested.

Please do not hesitate to contact me should you have any questions. Thank you.

Target Market(s)

Western speaking people aged from 25 to 60 from modest backgrounds to well off individuals

Industry/Entity Type

Real Estate

Requirements
Must have
• Professional in appearance, show a mature and trustworthy image
Should not have
• As there is good colour with the logo, i am do not want over the top designs or colours

```html
<!DOCTYPE html>
<html lang="en">
<head>
<meta charset="utf-8">
<title>brightkeyhomes stationery pack</title>
<link href="https://fonts.googleapis.com/css2?family=Hind:wght@400;500;600&family=Open+Sans:ital,wght@0,400;0,600;0,700;1,400&display=swap" rel="stylesheet">
<style>
:root{
  --bg:#e8e5e1;
  --paper:#ffffff;
  --ink:#3b3f48;
  --muted:#6d717a;
  --rule:#8a8d93;
  --red:#d7282f;
  --blue:#1f74bb;
  --green:#2e9a47;
  --band:#2b3a4e;
}
*{box-sizing:border-box;margin:0;padding:0}
html,body{width:1200px;height:900px;overflow:hidden}
body{background:var(--bg);font-family:"Open Sans",Arial,sans-serif;color:var(--ink);position:relative}
.sheet{position:absolute;background:var(--paper);box-shadow:0 2px 6px rgba(0,0,0,.18);overflow:hidden}
.brand{position:absolute;display:flex;align-items:center;gap:4px;font-family:"Hind",Arial,sans-serif;font-weight:600;color:var(--ink);white-space:nowrap;letter-spacing:-.2px}
.brand-dot{border-radius:50%;background:var(--blue);flex:none}
.footer-band{position:absolute;left:0;right:0;bottom:0;background:var(--band)}
.contact{position:absolute;font-size:5.2px;line-height:6.3px;color:var(--ink);list-style:none;white-space:nowrap}
.contact li{display:flex;align-items:center;gap:3px}
.ico{width:5px;height:5px;flex:none}
.web{font-size:5.5px;position:absolute;color:var(--ink)}
.web b{color:var(--red);font-weight:400}
.fax-title{position:absolute;font-weight:700;font-size:10px;color:var(--ink)}
.fax-table{position:absolute;border-collapse:collapse;font-size:5.2px}
.fax-table td{border:.6px solid var(--rule);height:11px;padding:0 3px;color:var(--ink)}
.fax-table td.l{background:#f3f3f3}
.flags{position:absolute;display:flex;border:.6px solid var(--rule);font-size:5.2px;background:#eee}
.flags span{flex:1;text-align:center;line-height:10px;border-right:.6px solid var(--rule)}
.flags span:last-child{border-right:0}
.comments{position:absolute;border:.6px solid var(--rule);font-size:4.8px;text-align:center;padding-top:8px}
.checks{position:absolute;display:flex;gap:10px;font-size:5.2px}
.checks span{display:flex;align-items:center;gap:3px}
.checks i{width:5px;height:5px;border:.6px solid var(--rule);display:block}
.photo{position:absolute;background:linear-gradient(180deg,#8fa1b5,#3d4656)}
.name{position:absolute;font-weight:700;font-size:8.5px;color:var(--red)}
.role{position:absolute;font-size:7px;color:var(--green);font-weight:600}
.accent{color:var(--blue)}
.compliments{position:absolute;font-style:italic;font-size:12px;color:var(--muted)}
.env{position:absolute;background:var(--paper);box-shadow:0 2px 6px rgba(0,0,0,.2)}
.flap{position:absolute;left:0;top:0}
.window{position:absolute;border:1px solid #b8bbc0;border-radius:5px;background:linear-gradient(180deg,#fafafa,#d9dadc)}
.address{position:absolute;font-size:6.2px;color:var(--ink);white-space:nowrap}
</style>
</head>
<body>

<svg width="0" height="0" style="position:absolute">
  <defs>
    <symbol id="i-pin" viewBox="0 0 10 10"><path d="M5 0a3.6 3.6 0 0 0-3.6 3.6C1.4 6.3 5 10 5 10s3.6-3.7 3.6-6.4A3.6 3.6 0 0 0 5 0zm0 5a1.4 1.4 0 1 1 0-2.8A1.4 1.4 0 0 1 5 5z" fill="#d7282f"/></symbol>
    <symbol id="i-mob" viewBox="0 0 10 10"><rect x="2.5" y="0.5" width="5" height="9" rx="1" fill="none" stroke="#d7282f" stroke-width="1.2"/></symbol>
    <symbol id="i-tel" viewBox="0 0 10 10"><path d="M1 3.5C1 2 3 1 5 1s4 1 4 2.5L7.5 4.3 6.6 3H3.4L2.5 4.3zM2 5h6v4H2z" fill="#d7282f"/></symbol>
    <symbol id="i-mail" viewBox="0 0 10 10"><rect x="0.6" y="2" width="8.8" height="6" fill="none" stroke="#d7282f" stroke-width="1.1"/><path d="M.6 2 5 5.6 9.4 2" fill="none" stroke="#d7282f" stroke-width="1.1"/></symbol>
    <symbol id="i-web" viewBox="0 0 10 10"><circle cx="5" cy="5" r="4.2" fill="none" stroke="#d7282f" stroke-width="1.2"/><path d="M.8 5h8.4M5 .8c-2.4 2.6-2.4 5.8 0 8.4M5 .8c2.4 2.6 2.4 5.8 0 8.4" fill="none" stroke="#d7282f" stroke-width=".8"/></symbol>
  </defs>
</svg>

<!-- Letterhead -->
<section class="sheet letterhead" style="left:18px;top:45px;width:272px;height:388px">
  <div class="brand" style="left:30px;top:56px;font-size:12px"><span class="brand-dot" style="width:8px;height:8px"></span>brightkeyhomes</div>
  <ul class="contact" style="left:176px;top:37px">
    <li><svg class="ico"><use href="#i-pin"/></svg><span>Shop 4, 52 harbour pde,</span></li>
    <li style="padding-left:8px">coral bay shore qld 4570</li>
    <li><svg class="ico"><use href="#i-mob"/></svg><span>0412 558 019</span></li>
    <li><svg class="ico"><use href="#i-tel"/></svg><span>07 5400 2176</span></li>
    <li><svg class="ico"><use href="#i-mail"/></svg><span>daniel@brightkeyhomes.com.au</span></li>
    <li><svg class="ico"><use href="#i-web"/></svg><span>www.brightkeyhomes.com.au</span></li>
  </ul>
  <div class="footer-band" style="height:9px"></div>
</section>

<!-- Letterhead, centred -->
<section class="sheet letterhead-centred" style="left:305px;top:35px;width:294px;height:416px">
  <div class="brand" style="left:0;right:0;justify-content:center;top:80px;font-size:17px"><span class="brand-dot" style="width:10px;height:10px"></span>brightkeyhomes</div>
  <div class="web" style="left:0;right:0;text-align:center;top:390px">www.<b>brightkeyhomes</b>.com.au</div>
  <div class="footer-band" style="height:10px"></div>
</section>

<!-- Fax, with comments box -->
<section class="sheet fax" style="left:613px;top:47px;width:276px;height:390px">
  <div class="brand" style="left:18px;top:50px;font-size:11px"><span class="brand-dot" style="width:7px;height:7px"></span>brightkeyhomes</div>
  <ul class="contact" style="left:195px;top:28px;font-size:4.8px;line-height:6px">
    <li><svg class="ico"><use href="#i-pin"/></svg><span>Shop 4, 52 harbour pde,</span></li>
    <li style="padding-left:8px">coral bay shore qld 4570</li>
    <li><svg class="ico"><use href="#i-tel"/></svg><span>07 5400 2176</span></li>
    <li><svg class="ico"><use href="#i-mail"/></svg><span>daniel@brightkeyhomes.com.au</span></li>
    <li><svg class="ico"><use href="#i-web"/></svg><span>www.brightkeyhomes.com.au</span></li>
  </ul>
  <div class="fax-title" style="left:241px;top:80px">FAX</div>
  <table class="fax-table" style="left:18px;top:96px;width:243px">
    <tr><td class="l" style="width:47px">To:</td><td style="width:88px"></td><td class="l" style="width:47px">From:</td><td></td></tr>
    <tr><td class="l">Fax:</td><td></td><td class="l">Pages:</td><td></td></tr>
    <tr><td class="l">Phone:</td><td></td><td class="l">Date:</td><td></td></tr>
    <tr><td class="l">Re:</td><td></td><td class="l">CC:</td><td></td></tr>
  </table>
  <div class="flags" style="left:18px;top:162px;width:243px"><span>Urgent</span><span>For Review</span><span>Please comment</span><span>Please Reply</span><span>Please Recycle</span></div>
  <div class="comments" style="left:18px;top:172px;width:243px;height:170px">COMMENTS</div>
  <div class="footer-band" style="height:10px"></div>
</section>

<!-- Fax, with tick boxes -->
<section class="sheet fax" style="left:905px;top:47px;width:275px;height:390px">
  <div class="brand" style="left:20px;top:50px;font-size:11px"><span class="brand-dot" style="width:7px;height:7px"></span>brightkeyhomes</div>
  <ul class="contact" style="left:195px;top:28px;font-size:4.8px;line-height:6px">
    <li><svg class="ico"><use href="#i-pin"/></svg><span>Shop 4, 52 harbour pde,</span></li>
    <li style="padding-left:8px">coral bay shore qld 4570</li>
    <li><svg class="ico"><use href="#i-tel"/></svg><span>07 5400 2176</span></li>
    <li><svg class="ico"><use href="#i-mail"/></svg><span>daniel@brightkeyhomes.com.au</span></li>
    <li><svg class="ico"><use href="#i-web"/></svg><span>www.brightkeyhomes.com.au</span></li>
  </ul>
  <div class="fax-title" style="left:240px;top:80px">FAX</div>
  <table class="fax-table" style="left:20px;top:96px;width:241px">
    <tr><td class="l" style="width:45px">To:</td><td style="width:88px"></td><td class="l" style="width:45px">From:</td><td></td></tr>
    <tr><td class="l">Fax:</td><td></td><td class="l">Pages:</td><td></td></tr>
    <tr><td class="l">Phone:</td><td></td><td class="l">Date:</td><td></td></tr>
    <tr><td class="l">Re:</td><td></td><td class="l">CC:</td><td></td></tr>
  </table>
  <div class="checks" style="left:20px;top:148px"><span><i></i>Urgent</span><span><i></i>For Review</span><span><i></i>Please comment</span><span><i></i>Please Reply</span><span><i></i>Please Recycle</span></div>
  <div class="footer-band" style="height:10px"></div>
</section>

<!-- Business card, front -->
<section class="sheet card-front" style="left:30px;top:476px;width:266px;height:151px">
  <div class="photo" role="img" aria-label="Portrait photo of the principal" style="left:130px;top:25px;width:41px;height:50px"></div>
  <div class="name" style="left:178px;top:40px">Daniel Marsh</div>
  <div class="role" style="left:178px;top:53px">Principal</div>
  <ul class="contact" style="left:128px;top:83px;font-size:5.6px;line-height:10.5px">
    <li><svg class="ico" style="width:6px;height:6px"><use href="#i-mob"/></svg><span>0412 558 019</span></li>
    <li><svg class="ico" style="width:6px;height:6px"><use href="#i-tel"/></svg><span>07 5400 2176</span></li>
    <li><svg class="ico" style="width:6px;height:6px"><use href="#i-mail"/></svg><span>daniel@<span class="accent">brightkeyhomes</span>.com.au</span></li>
    <li><svg class="ico" style="width:6px;height:6px"><use href="#i-pin"/></svg><span>shop 4, 52 harbour pde, coral bay shore qld 4570</span></li>
    <li style="margin-top:3px"><svg class="ico" style="width:6px;height:6px"><use href="#i-web"/></svg><span>www.<span class="accent">brightkeyhomes</span>.com.au</span></li>
  </ul>
</section>

<!-- Business card, back -->
<section class="sheet card-back" style="left:318px;top:474px;width:273px;height:156px">
  <div class="brand" style="left:0;right:0;justify-content:center;top:78px;font-size:14px"><span class="brand-dot" style="width:9px;height:9px"></span>brightkeyhomes</div>
  <div class="footer-band" style="height:9px"></div>
</section>

<!-- With compliments slip -->
<section class="sheet compliments-slip" style="left:93px;top:655px;width:405px;height:191px">
  <div class="brand" style="left:22px;top:68px;font-size:15px"><span class="brand-dot" style="width:9px;height:9px"></span>brightkeyhomes</div>
  <div class="compliments" style="left:279px;top:35px">With Compliments</div>
  <div class="footer-band" style="height:13px"></div>
</section>

<!-- Envelopes, backs with coloured flaps -->
<section class="env env-green" style="left:630px;top:462px;width:445px;height:258px">
  <svg class="flap" width="445" height="72" viewBox="0 0 445 72"><path d="M0 0H445V14C370 22 270 58 222 70 175 58 75 22 0 14Z" fill="var(--green)"/><circle cx="222" cy="32" r="15" fill="#fff"/></svg>
</section>
<section class="env env-blue" style="left:662px;top:525px;width:446px;height:230px">
  <svg class="flap" width="446" height="72" viewBox="0 0 446 72"><path d="M0 0H446V14C370 22 270 58 223 70 176 58 76 22 0 14Z" fill="var(--blue)"/><circle cx="223" cy="32" r="15" fill="#fff"/></svg>
</section>
<section class="env env-red" style="left:693px;top:590px;width:458px;height:220px">
  <svg class="flap" width="458" height="72" viewBox="0 0 458 72"><path d="M0 0H458V14C380 22 278 58 229 70 180 58 78 22 0 14Z" fill="var(--red)"/><circle cx="229" cy="32" r="15" fill="#fff"/></svg>
</section>

<!-- Envelope, front -->
<section class="sheet env-front" style="left:726px;top:664px;width:446px;height:195px">
  <div class="brand" style="left:50px;top:64px;font-size:14px"><span class="brand-dot" style="width:9px;height:9px"></span>brightkeyhomes</div>
  <div class="address" style="left:38px;top:99px">Shop 4, 52 harbour pde, coral bay shore qld 4570</div>
  <div class="window" style="left:32px;top:113px;width:138px;height:40px"></div>
  <ul class="contact" style="left:316px;top:38px;font-size:6px;line-height:7.5px">
    <li><svg class="ico"><use href="#i-tel"/></svg><span>07 5400 2176</span></li>
    <li><svg class="ico"><use href="#i-mail"/></svg><span>daniel@brightkeyhomes.com.au</span></li>
    <li><svg class="ico"><use href="#i-web"/></svg><span>www.brightkeyhomes.com.au</span></li>
  </ul>
  <div class="footer-band" style="height:13px"></div>
</section>

</body>
</html>
```